Veltrane Group Business Card Design

The CEO is looking for a new trendy look for his business card.
You can stay with current branding or come up with something new/creative. It can be 3D, including Medical Office buildings. You can use our logo in a variety of colors. Please include name, title, company name, company website, email address, cell number

Target Market(s)

Real Estate Development and Construction

Industry/Entity Type

Health care real estate

Contact Information for Business Card

Rohesh Kamdar, CEO M-604.781.2249 E-roheshkamdar@veltrane.com Address:4180 Lindqvist Ave, Tampa, FL 33482 www.veltrane.com

Font styles to use
Other font styles liked:
• Be creative

Requirements
Must have
• Creative, trendy look
Nice to have
• Please go to our website to get a feel- www. veltrane.com
Should not have
• small fonts

```html
<!DOCTYPE html>
<html lang="en">
<head>
<meta charset="utf-8">
<title>Veltrane Group Business Card</title>
<link href="https://fonts.googleapis.com/css2?family=Montserrat:wght@400;500;700;800;900&display=swap" rel="stylesheet">
<style>
  :root {
    --brand-red: #b01f2a;
    --brand-navy: #1b2f52;
    --card-white: #ffffff;
    --ink-grey: #3a3a3a;
    --backdrop: #262626;
  }
  * { margin: 0; padding: 0; box-sizing: border-box; }
  html, body {
    width: 1200px; height: 874px; overflow: hidden;
    background: var(--backdrop);
    font-family: "Montserrat", sans-serif;
  }
  .stage {
    width: 1200px; height: 874px;
    display: flex; flex-direction: column;
    align-items: center; justify-content: center; gap: 50px;
  }
  .card {
    position: relative;
    width: 620px; height: 354px;
    background: var(--card-white);
    border-radius: 22px;
    overflow: hidden;
  }
  .wordmark {
    color: var(--brand-red);
    font-weight: 900;
    line-height: 0.95;
    letter-spacing: -0.03em;
    text-align: right;
  }
  .card-front .wordmark {
    position: absolute; left: 0; right: 0; top: 92px;
    text-align: center;
    font-size: 96px;
  }
  .card-back .backdrop-shape {
    position: absolute; inset: 0;
    width: 620px; height: 354px;
  }
  .card-back .wordmark {
    position: absolute; right: 40px; top: 78px;
    font-size: 46px;
  }
  .contact-list {
    position: absolute; left: 26px; top: 194px;
    list-style: none;
    color: var(--card-white);
    font-size: 14px; font-weight: 400; line-height: 1.25;
  }
  .contact-list li {
    display: flex; align-items: flex-start; gap: 8px;
    margin-bottom: 7px;
  }
  .contact-list svg { flex: none; width: 13px; height: 13px; margin-top: 2px; }
  .holder {
    position: absolute; right: 44px; top: 258px;
    text-align: right;
  }
  .holder-name {
    color: var(--brand-red);
    font-size: 22px; font-weight: 800; letter-spacing: 0.02em;
    white-space: nowrap;
  }
  .holder-title {
    color: var(--ink-grey);
    font-size: 17px; font-weight: 500; margin-top: 4px;
  }
  .accent-bar {
    position: absolute; right: 0; top: 262px;
    width: 22px; height: 54px;
    background: var(--brand-red);
  }
</style>
</head>
<body>
<main class="stage">
  <section class="card card-front" aria-label="Card front">
    <div class="wordmark">Veltrane<br>Group</div>
  </section>

  <section class="card card-back" aria-label="Card back">
    <svg class="backdrop-shape" viewBox="0 0 620 354" aria-hidden="true">
      <path d="M0 0 H18 C40 120 276 150 300 354 H0 Z" fill="var(--brand-navy)"/>
      <path d="M18 0 C40 120 276 150 300 354" fill="none" stroke="var(--card-white)" stroke-width="4"/>
      <path d="M22 0 H30 C80 100 312 130 316 354 H304 C280 150 46 116 22 0 Z" fill="var(--brand-red)"/>
    </svg>

    <div class="wordmark">Veltrane<br>Group</div>

    <ul class="contact-list">
      <li>
        <svg viewBox="0 0 12 12"><path d="M6 0.5a4 4 0 0 1 4 4c0 3-4 7-4 7s-4-4-4-7a4 4 0 0 1 4-4z" fill="var(--brand-red)"/><circle cx="6" cy="4.5" r="1.5" fill="var(--brand-navy)"/></svg>
        <span>4180 Lindqvist Ave,<br>Tampa, FL 33482</span>
      </li>
      <li>
        <svg viewBox="0 0 12 12"><rect x="3" y="0.5" width="6" height="11" rx="1.2" fill="var(--brand-red)"/><rect x="4" y="2" width="4" height="7" fill="var(--brand-navy)"/></svg>
        <span>604.781.2249</span>
      </li>
      <li>
        <svg viewBox="0 0 12 12"><rect x="0.5" y="2.5" width="11" height="7" rx="1" fill="var(--brand-red)"/><path d="M1 3 L6 7 L11 3" fill="none" stroke="var(--brand-navy)" stroke-width="1"/></svg>
        <span>roheshkamdar@veltrane.com</span>
      </li>
      <li>
        <svg viewBox="0 0 12 12"><circle cx="6" cy="6" r="5.5" fill="var(--brand-red)"/><path d="M0.5 6 H11.5 M6 0.5 C3 3 3 9 6 11.5 M6 0.5 C9 3 9 9 6 11.5" fill="none" stroke="var(--brand-navy)" stroke-width="0.8"/></svg>
        <span>www.veltrane.com</span>
      </li>
    </ul>

    <div class="holder">
      <div class="holder-name">ROHESH KAMDAR</div>
      <div class="holder-title">CEO</div>
    </div>
    <div class="accent-bar"></div>
  </section>
</main>
</body>
</html>
```